Unternehmensbroschüre
Zielgruppe
Unternehmen
Aufgabenstellung
Gestalten Sie aus dem gelieferten Text eine exklusive 12-seitige Unternehmensbroschüre im Premium-Stil. Die Broschüre richtet sich an Geschäftsführer und HR-Verantwortliche von Schweizer KMU. Sie soll sich nicht wie Werbung, sondern wie ein hochwertiges Markenmagazin oder Manifest lesen.
Designvorgaben:
Minimalistisch, elegant und zeitlos.
Viel Weissraum.
Grosse, starke Typografie.
Ruhiges Schweizer Design (Quern, Vostra, Malvent, Ordevina als Inspiration).
Keine überladenen Layouts.
Keine typischen Business-Stockfotos.
Maximal 3–4 emotionale Bilder in der gesamten Broschüre.
Wo möglich, mit grafischen Elementen statt Fotos arbeiten.
Jede Doppelseite soll einen eigenen Rhythmus und Charakter haben.
Farben: Weiss, Anthrazit, Türkis als Akzent, Gold sehr sparsam.
Das KoruMed-Logo und die Markenidentität sollen dezent und hochwertig integriert werden.
Ziel: Der Geschäftsführer soll die Broschüre nicht nur lesen, sondern bis zur letzten Seite in der Hand behalten und das Gefühl haben, Teil einer neuen Gesundheitsbewegung werden zu können.

```html
<!DOCTYPE html>
<html lang="de">
<head>
<meta charset="utf-8">
<title>KoruMed Broschüre – Pilotprogramm 2026</title>
<link href="https://fonts.googleapis.com/css2?family=Montserrat:wght@700;800;900&family=Poppins:wght@300;400;600;700&display=swap" rel="stylesheet">
<style>
:root{
  --teal:#2a9d93;
  --teal-dark:#21857c;
  --gold:#c9a02a;
  --gold-soft:#d8b555;
  --anthracite:#1f1f1f;
  --ink:#333;
  --muted:#666;
  --white:#fff;
  --stage:#dedede;
}
*{box-sizing:border-box;margin:0;padding:0}
html,body{width:1200px;height:3000px;overflow:hidden}
body{background:var(--stage);font-family:"Poppins",sans-serif;color:var(--ink);position:relative}
.page{position:absolute;width:500px;height:707px;background:var(--white);overflow:hidden}
.cover{left:350px;top:34px;box-shadow:0 8px 24px rgba(0,0,0,.18)}
.spread{position:absolute;left:100px;width:1000px;height:707px;box-shadow:0 8px 24px rgba(0,0,0,.18)}
.spread .left{left:0}
.spread .right{left:500px}
.spread-1{top:775px}
.spread-2{top:1516px}
.spread-3{top:2257px}
.abs{position:absolute}
.display{font-family:"Montserrat",sans-serif;font-weight:900;line-height:1.05}
.h-gold{font-family:"Montserrat",sans-serif;font-weight:800;color:var(--gold);text-transform:uppercase}
.h-teal{font-family:"Montserrat",sans-serif;font-weight:800;color:var(--teal)}
.body{font-size:8px;line-height:1.6;color:var(--muted);font-weight:300}
.body b{font-weight:600;color:var(--teal)}
.photo{position:absolute}
.teal-bar{position:absolute;left:0;right:0;bottom:0;height:34px;background:var(--teal);color:#fff;font-family:"Montserrat",sans-serif;font-weight:800;font-size:10px;display:flex;align-items:center;justify-content:center;gap:8px}
.teal-bar .dot{color:var(--gold-soft)}
/* cover */
.cover-visual{left:0;top:0;width:500px;height:390px;background:linear-gradient(160deg,#f3dca0 0%,#d9a84b 35%,#c98a2c 55%,#e9c982 75%,#f7ecd0 100%)}
.brand{position:absolute;top:34px;right:36px;display:flex;align-items:center;gap:7px;font-family:"Poppins",sans-serif;font-weight:700;font-size:22px;color:var(--teal);letter-spacing:.5px}
.brand i{display:block;width:16px;height:16px;border-radius:50%;background:var(--teal)}
.cover-title{left:60px;top:290px;right:0;height:140px;background:var(--teal);color:#fff;padding:18px 24px}
.cover-title .kicker{font-family:"Montserrat",sans-serif;font-weight:700;font-size:15px;letter-spacing:.5px}
.cover-title .big{font-size:38px;letter-spacing:.5px}
.cover-lead{left:60px;top:452px;width:410px;font-weight:700;font-size:13px;line-height:1.4;color:var(--gold)}
.pilot{left:60px;top:540px;color:var(--gold);font-family:"Montserrat",sans-serif;font-weight:800}
.pilot span{display:block;font-size:14px}
.pilot strong{display:block;font-size:40px;font-weight:900;line-height:1}
.cover-note{left:255px;top:548px;width:200px;font-size:8.5px;line-height:1.5;color:var(--muted);border-left:1px solid #ccc;padding-left:10px}
.cover-band{left:230px;top:622px;right:0;height:22px;background:var(--gold);color:#fff;font-size:8px;display:flex;align-items:center;padding-left:14px}
.cover-mark{left:60px;top:652px;font-family:"Montserrat",sans-serif;font-weight:800;font-size:17px;color:var(--teal)}
/* spread 1 left */
.s1-head{left:40px;top:58px;font-size:20px}
.s1-col{left:40px;top:110px;width:220px}
.s1-col h3{font-size:12px;line-height:1.3;margin-bottom:5px}
.s1-col p{margin-bottom:14px}
.consequences{left:290px;top:108px;width:180px}
.consequences h3{font-size:12px;margin-bottom:10px}
.consequences li{list-style:none;font-family:"Montserrat",sans-serif;font-weight:700;font-size:8.5px;color:var(--anthracite);margin-bottom:15px;display:flex;gap:9px;align-items:center}
.consequences li::before{content:"";width:5px;height:5px;border-radius:50%;background:var(--gold)}
.s1-visual{left:0;top:300px;width:500px;height:407px;background:linear-gradient(180deg,#f1b45e 0%,#d47a2e 25%,#6d3f22 45%,#1f1b19 60%,#1c1c1c 100%)}
.s1-claims{left:40px;top:520px;width:300px;font-family:"Montserrat",sans-serif;font-weight:800;font-size:13.5px;line-height:1.3;color:var(--gold)}
.s1-claims p{margin-bottom:10px}
.s1-foot{left:40px;bottom:22px;font-family:"Montserrat",sans-serif;font-weight:700;font-size:8.5px;color:var(--teal)}
.blob{left:335px;top:470px;width:150px;height:160px}
/* spread 1 right */
.s1r-head{left:0;right:0;top:38px;text-align:center;font-size:14px}
.s1r-sub{left:0;right:0;top:60px;text-align:center;font-size:10.5px}
.clock{left:0;top:90px;width:500px;height:440px;background:radial-gradient(ellipse at 50% 95%,#f4f4f4 0%,#d9d9d9 45%,#fff 72%)}
.clock-words{left:180px;top:135px;width:140px;text-align:center;color:var(--teal);font-family:"Montserrat",sans-serif;font-weight:800}
.clock-words small{display:block;font-size:8px;font-weight:600}
.clock-words span{display:block;font-size:17px;line-height:1.15}
.s1r-left{left:38px;top:142px;width:110px}
.s1r-right{left:340px;top:140px;width:130px}
.values{left:0;top:530px;width:500px;height:177px;background:var(--teal);color:#fff;padding:22px 34px 0}
.values-row{display:flex;gap:26px}
.value{flex:1}
.value-head{display:flex;align-items:center;gap:8px;font-family:"Montserrat",sans-serif;font-weight:800;font-size:9px;line-height:1.2;margin-bottom:12px}
.icon{width:24px;height:24px;border-radius:50%;background:var(--gold);display:flex;align-items:center;justify-content:center;flex:none}
.value p{font-size:8px;line-height:1.55;font-weight:300}
.values .note{position:absolute;left:0;right:0;bottom:22px;text-align:center;font-family:"Montserrat",sans-serif;font-weight:700;font-size:9px}
/* spread 2 left */
.s2-head{left:40px;top:70px;width:240px;font-size:21px;line-height:1.15}
.s2-sub{left:40px;top:170px;width:250px;font-size:12px;line-height:1.3}
.s2-body{left:40px;top:215px;width:240px}
.s2-body p{margin-bottom:10px}
.s2-column{left:300px;top:0;width:200px;height:480px;background:var(--teal);color:#fff;padding:56px 22px 0}
.s2-column h4{font-family:"Montserrat",sans-serif;font-weight:800;font-size:9px;line-height:1.6;margin-bottom:6px}
.s2-column p{font-size:8px;line-height:1.7;font-weight:300;margin-bottom:14px}
.s2-visual{left:0;top:480px;width:500px;height:227px;background:linear-gradient(135deg,#e9c98b 0%,#c88f45 45%,#8a6a4a 75%,#d9b47a 100%)}
.s2-circle{left:270px;top:500px;width:170px;height:170px;border-radius:50%;background:var(--gold);color:#fff;display:flex;align-items:center;justify-content:center;text-align:center;padding:24px;font-family:"Montserrat",sans-serif;font-weight:800;font-size:10px;line-height:1.4}
/* spread 2 right */
.s2r-head{left:0;right:0;top:44px;text-align:center;font-size:16px;line-height:1.35}
.pioneer-box{left:36px;top:104px;width:428px;height:318px;border:1px solid var(--gold-soft);border-radius:6px;padding:20px 22px}
.pioneer-cols{display:flex;gap:22px}
.pioneer-cols .body{flex:1;line-height:2.05;color:var(--anthracite)}
.pioneer-cols h3{font-size:17px;line-height:1.15;margin-bottom:10px}
.pioneer-q{margin-top:18px;font-family:"Montserrat",sans-serif;font-weight:800;font-size:22px;line-height:1.3}
.pioneer-q .t{color:var(--teal)}
.pioneer-q .g{color:var(--gold)}
.s2r-visual{left:0;top:440px;width:500px;height:267px;background:linear-gradient(180deg,#cdd6df 0%,#f1c37a 30%,#5b6676 60%,#1f2a37 100%)}
/* spread 3 left */
.s3-head{left:40px;top:62px;font-size:16px}
.s3-visual{left:200px;top:150px;width:300px;height:523px;background:linear-gradient(180deg,#ffffff 0%,#eef1f4 45%,#c9d0d8 80%,#7d8896 100%)}
.s3-now{left:40px;top:100px;color:var(--teal)}
.s3-now .n1{font-size:46px}
.s3-now .n2{position:absolute;left:170px;top:14px;font-size:17px;white-space:nowrap}
.s3-now .n3{position:absolute;left:4px;top:86px;font-size:17px}
.s3-now .n4{position:absolute;left:115px;top:52px;font-size:52px;color:var(--gold)}
.gain{left:40px;width:180px}
.gain h4{display:flex;align-items:center;gap:8px;font-family:"Montserrat",sans-serif;font-weight:800;font-size:11px;color:var(--teal);margin-bottom:6px}
.gain li{list-style:none;font-size:8px;line-height:1.8;color:var(--muted);padding-left:12px;position:relative}
.gain li::before{content:"";position:absolute;left:2px;top:6px;width:4px;height:4px;border-radius:50%;background:var(--gold)}
.s3-brand{left:330px;top:590px;width:150px;text-align:right}
.s3-brand b{display:block;font-family:"Montserrat",sans-serif;font-weight:800;font-size:12px;color:var(--gold)}
.s3-brand span{font-size:7px;line-height:1.5;color:var(--muted)}
/* spread 3 right */
.dark{background:var(--anthracite)}
.s3r-visual{left:0;top:0;width:190px;height:673px;background:linear-gradient(180deg,#1f4f8a 0%,#4c7fb8 35%,#9db4c9 60%,#e2a15a 80%,#2a2420 100%)}
.s3r-claim{left:30px;top:300px;width:160px;font-family:"Montserrat",sans-serif;font-weight:800;font-size:17px;line-height:1.35;color:#fff}
.s3r-text{left:215px;top:42px;width:250px;color:#cfcfcf;font-size:7.5px;line-height:1.5;font-weight:300}
.s3r-text p{margin-bottom:9px}
.divider{height:1px;background:#555;margin:14px 0 16px}
.invest{margin-bottom:14px}
.invest h5{display:flex;align-items:center;gap:9px;font-family:"Montserrat",sans-serif;font-weight:700;font-size:8px;color:var(--teal);margin-bottom:6px}
.invest .icon{width:20px;height:20px}
</style>
</head>
<body>

<!-- Cover -->
<section class="page cover">
  <div class="photo cover-visual" role="img" aria-label="Aquarell einer goldenen Flusslandschaft mit Wegen und Bäumen"></div>
  <div class="brand"><i></i>Altessa</div>
  <div class="abs cover-title">
    <div class="kicker">GESUNDE MITARBEITENDE</div>
    <div class="display big">BRAUCHEN<br>ORIENTIERUNG.</div>
  </div>
  <p class="abs cover-lead">Manchmal braucht Gesundheit nicht noch mehr Methoden. Sondern eine neue Richtung. Gemeinsam mit Unternehmen geht KoruMed diesen Weg.</p>
  <div class="abs pilot"><span>Pilotprogramm</span><strong>2026</strong></div>
  <p class="abs cover-note">Für Unternehmen, die Betriebliches Gesundheits­management neu denken.</p>
  <div class="abs cover-band">Der Verein für eine solidarische Gesundheitsversorgung.</div>
  <div class="abs cover-mark">KoruMed</div>
</section>

<!-- Spread 1 -->
<section class="spread spread-1">
  <div class="page left">
    <h2 class="abs h-gold s1-head">Gesunde Mitarbeitende</h2>
    <div class="abs s1-col">
      <h3 class="h-teal">Überforderung ist kein Gefühl.<br>Sie ist ein Kostenfaktor.</h3>
      <p class="body">Ein modernes Unternehmen muss in Digitalisierung, Prozesse und Wachstum investieren.</p>
      <h3 class="h-teal">Doch High-Tech funktioniert<br>nur mit High-Human.</h3>
      <p class="body">Fehlt Orientierung, wird aus Belastung Überforderung. Aus Motivation wird Erschöpfung. Aus Leistung werden Fehlzeiten.</p>
    </div>
    <div class="abs consequences">
      <h3 class="h-teal">Die Folgen.</h3>
      <ul>
        <li>Steigende Absenzen</li>
        <li>Innere Kündigung</li>
        <li>Fachkräftemangel</li>
        <li>Sinkende Motivation</li>
        <li>Höhere Fluktuation</li>
        <li>Steigende Gesundheitskosten</li>
      </ul>
    </div>
    <div class="photo s1-visual" role="img" aria-label="Silhouette eines Menschen mit ausgebreiteten Armen auf einem Berg im Sonnenuntergang"></div>
    <svg class="abs blob" viewBox="0 0 150 160" aria-hidden="true">
      <defs><linearGradient id="blobFill" x1="0" y1="0" x2="1" y2="1"><stop offset="0" stop-color="#e69a2e"/><stop offset="1" stop-color="#b8451f"/></linearGradient></defs>
      <path d="M80 4C118 6 146 48 146 92c0 44-30 66-72 64C32 154 4 132 6 98 8 60 40 2 80 4z" fill="url(#blobFill)"/>
      <foreignObject x="22" y="50" width="112" height="80"><div xmlns="http://www.w3.org/1999/xhtml" style="font-family:Montserrat,sans-serif;font-weight:700;font-size:7px;line-height:1.5;color:#fff;text-align:center">Getragen von einer Gemeinschaft, die Gesundheit bildbar macht, bevor Krankheit entsteht.</div></foreignObject>
    </svg>
    <div class="abs s1-claims">
      <p>Deshalb braucht Gesundheit<br>einen neuen Blick.</p>
      <p>Nicht Einzelmassnahmen.<br>Kontinuität.</p>
      <p>Kontinuität schafft Vertrauen.</p>
      <p>Vertrauen schafft Veränderung.</p>
    </div>
    <p class="abs s1-foot">Burn-Out beginnt nicht an einem einzigen Tag. Gesundheit aber auch nicht.</p>
  </div>

  <div class="page right">
    <h2 class="abs h-gold s1r-head">Zeit ist die neue Währung der Wertschätzung.</h2>
    <p class="abs h-teal s1r-sub">Gesundheitszeit statt Ausfallzeit.</p>
    <div class="photo clock" role="img" aria-label="Nahaufnahme einer silbernen Taschenuhr mit Zifferblatt"></div>
    <div class="abs clock-words">
      <small>ihre</small><span>Lebenszeit.</span>
      <small>ihre</small><span>Energie.</span>
    </div>
    <p class="abs body s1r-left">Mitarbeitende schenken ihrem Unternehmen jeden Tag das Wertvollste, das sie besitzen.</p>
    <p class="abs body s1r-right">Wer heute Höchstleistung erwartet, muss <b>zuerst Energie zurückgeben.</b> Wenn Sie Ihrem Team gezielt Gesundheitszeit ermöglichen, verändern Sie mehr als Gesundheit. Sie investieren nicht in ein BGM-Konzept.<br><br><b>Sie investieren in das Herz Ihrer Firma: den Menschen.</b></p>
    <div class="abs values">
      <div class="values-row">
        <div class="value">
          <div class="value-head"><span class="icon"><svg width="12" height="12" viewBox="0 0 12 12"><circle cx="6" cy="3" r="2" fill="#fff"/><path d="M2 11c0-3 2-5 4-5s4 2 4 5z" fill="#fff"/></svg></span>Menschlichkeit<br>erleben</div>
          <p>Wer sich als Mensch geschätzt fühlt, arbeitet nicht mehr nur für den Lohn.</p>
        </div>
        <div class="value">
          <div class="value-head"><span class="icon"><svg width="12" height="12" viewBox="0 0 12 12"><circle cx="6" cy="5" r="3.5" fill="none" stroke="#fff" stroke-width="1.4"/><path d="M4 8l-1 3.5 3-1.5 3 1.5-1-3.5" fill="#fff"/></svg></span>Loyalität<br>verankern</div>
          <p>Treue lässt sich nicht kaufen. Menschen vergessen nie, wer ihre Gesundheit schützt.</p>
        </div>
        <div class="value">
          <div class="value-head"><span class="icon"><svg width="12" height="12" viewBox="0 0 12 12"><path d="M6 11V5M6 5C6 2 9 1 10 1c0 2-1 4-4 4zM6 7C6 4 3 3 2 3c0 2 1 4 4 4z" fill="#fff" stroke="#fff" stroke-width="1"/></svg></span>Gesund<br>wachsen</div>
          <p>Unternehmen wachsen nicht durch Druck. Sie wachsen durch Menschen, die mit voller Kraft hinter ihnen stehen.</p>
        </div>
      </div>
      <p class="note">Burn-Out beginnt nicht an einem einzigen Tag. Gesundheit aber auch nicht.</p>
    </div>
  </div>
</section>

<!-- Spread 2 -->
<section class="spread spread-2">
  <div class="page left">
    <h2 class="abs h-gold s2-head">Warum ein<br>Verein statt<br>einer Firma?</h2>
    <p class="abs h-teal s2-sub">Gesundheit ist keine Frage des Profits. Sondern der Solidarität.</p>
    <div class="abs body s2-body">
      <p>KoruMed geht einen neuen Weg.</p>
      <p>Als Verein verzichten wir bewusst auf Gewinnmaximierung.</p>
      <p>Unser Ziel ist menschlicher.</p>
      <p>Wir schaffen eine Gesundheitsgemeinschaft, die verbindet.</p>
      <p>Verantwortung teilt.</p>
      <p>Und Gesundheit für alle zugänglich macht.</p>
    </div>
    <div class="abs s2-column">
      <h4>Solidarität öffnet Türen.<br>Mitarbeitende.<br>Unternehmen.<br>Navigatoren.<br>Gönner.<br>Partner.</h4>
      <p>Alle bewirken etwas.<br>Alle tragen Verantwortung.</p>
      <h4>Alle gewinnen.</h4>
      <h4 style="margin-top:14px">Der Solidaritätsfonds.</h4>
      <p>Jede Mitgliedschaft.<br>Jede Behandlung.<br>Jeder Unternehmensbeitrag.<br>Jeder Beitrag stärkt das gemeinsame Fundament.<br>So entstehen echte Gesundheitschancen.<br>Gerade dort, wo Prävention für alle erreichbar sein sollte.</p>
    </div>
    <div class="photo s2-visual" role="img" aria-label="Aquarell einer Gruppe von Menschen verschiedener Generationen im warmen Abendlicht"></div>
    <div class="abs s2-circle">Nicht jeder kann gleich viel geben. Aber jeder Beitrag hilft mit, Gesundheit für mehr Menschen Wirklichkeit werden zu lassen.</div>
  </div>

  <div class="page right">
    <h2 class="abs h-gold s2r-head">Das erste Unternehmen<br>verändert alles.</h2>
    <div class="abs pioneer-box">
      <div class="pioneer-cols">
        <p class="body">Es braucht keine hundert Unternehmen.<br>Nicht fünfzig.<br>Nicht zehn.<br>Es braucht genau eines.<br>Eines, das den Mut hat, Gesundheit radikal neu zu denken.<br>Eines, das Menschen mehr schenken will als nur einen Lohn.<br>Eines, das Verantwortung nicht delegiert, sondern im Alltag lebt.</p>
        <div>
          <h3 class="h-teal">Das Pionier-<br>Unternehmen</h3>
          <p class="body" style="line-height:2.05;color:var(--anthracite)">Sie gehören zu den Ersten.<br>Sie gestalten das Fundament mit.<br>Sie setzen ein unübersehbares Zeichen.<br>Für Ihr Team.<br>Für Ihre Region.<br>Für eine neue Kultur der Wertschätzung.</p>
        </div>
      </div>
      <p class="pioneer-q"><span class="t">Werden Sie dieses eine</span><br><span class="g">Pionierunternehmen?</span></p>
    </div>
    <div class="photo s2r-visual" role="img" aria-label="Silhouetten von Menschen im Gespräch vor einer Stadtsilhouette im Gegenlicht"></div>
  </div>
</section>

<!-- Spread 3 -->
<section class="spread spread-3">
  <div class="page left">
    <div class="photo s3-visual" role="img" aria-label="Silhouette eines Menschen mit erhobenen Armen auf einem Felsen vor Hochhäusern"></div>
    <h2 class="abs h-gold s3-head">Ein Beitrag. Vier Gewinner.</h2>
    <div class="abs display s3-now">
      <span class="n1">Nicht</span>
      <span class="n2">irgendwann.</span>
      <span class="n4">heute.</span>
      <span class="n3">Sondern</span>
    </div>
    <div class="abs gain" style="top:300px">
      <h4><span class="icon"><svg width="12" height="12" viewBox="0 0 12 12"><circle cx="4" cy="4" r="1.8" fill="#fff"/><circle cx="8" cy="4" r="1.8" fill="#fff"/><path d="M1 10c0-2 1.5-3.5 3-3.5S7 8 7 10zM5 10c0-2 1.5-3.5 3-3.5s3 1.5 3 3.5z" fill="#fff"/></svg></span>Ihr Team</h4>
      <ul><li>Gewinnt Gesundheit.</li><li>Wertvolle Zeit.</li><li>Klare Orientierung.</li></ul>
    </div>
    <div class="abs gain" style="top:390px">
      <h4><span class="icon"><svg width="12" height="12" viewBox="0 0 12 12"><path d="M6 11S2 7 2 4.5a4 4 0 018 0C10 7 6 11 6 11z" fill="#fff"/><circle cx="6" cy="4.5" r="1.5" fill="#c9a02a"/></svg></span>Ihre Region</h4>
      <ul><li>Gewinnt ein starkes Gesundheitsnetzwerk.</li><li>Gelebte Solidarität.</li><li>Mehr Zusammenhalt.</li></ul>
    </div>
    <div class="abs s3-brand"><b>KoruMed</b><span>gewinnt die Möglichkeit, Prävention genau dort zugänglich zu machen, wo der Zugang heute oft noch fehlt.</span></div>
    <div class="teal-bar">Ein Beitrag <span class="dot">•</span> Vier Gewinner <span class="dot">•</span> Eine gemeinsame Zukunft</div>
  </div>

  <div class="page right dark">
    <div class="photo s3r-visual" role="img" aria-label="Zwei Wanderer als Silhouette vor einer Felswand unter blauem Himmel"></div>
    <h2 class="abs s3r-claim">GESUNDHEIT<br>DARF SICH<br>RECHNEN.</h2>
    <div class="abs s3r-text">
      <p>Wirtschaftlicher Erfolg ist keine Frage von Excel-Tabellen.</p>
      <p>Sondern von Menschen mit Energie.</p>
      <p>Präsenz allein bewegt keine Unternehmen.</p>
      <p>Es ist die Energie der Menschen, die den Unterschied macht.</p>
      <p>KoruMed ist deshalb kein Kostenfaktor, sondern ein wichtiges</p>
      <p>Investment in die wichtigste Struktur des Unternehmens. Den Menschen.</p>
      <div class="divider"></div>
      <p>Sie investieren</p>
      <div class="invest">
        <h5><span class="icon"><svg width="10" height="10" viewBox="0 0 12 12"><path d="M6 1l4 1.5V6c0 3-2 4.5-4 5-2-.5-4-2-4-5V2.5z" fill="#fff"/></svg></span>in Performance-Sicherheit</h5>
        <p>Mentaler Fokus. Mehr Energie.<br>Mehr Leichtigkeit am Arbeitsplatz.</p>
      </div>
      <div class="invest">
        <h5><span class="icon"><svg width="10" height="10" viewBox="0 0 12 12"><path d="M6 10.5S1 7.5 1 4.3A2.5 2.5 0 016 3a2.5 2.5 0 015 1.3C11 7.5 6 10.5 6 10.5z" fill="#fff"/></svg></span>in Kultur-Anker</h5>
        <p>Ein Umfeld, das Gesundheit stärkt. Vertrauen schafft und Fachkräfte langfristig bindet.</p>
      </div>
      <div class="invest">
        <h5><span class="icon"><svg width="10" height="10" viewBox="0 0 12 12"><rect x="2.5" y="1" width="7" height="10" rx="1" fill="#fff"/><path d="M4 4h4M4 6h4M4 8h3" stroke="#c9a02a" stroke-width=".8"/></svg></span>in steueroptimierte Wertschätzung</h5>
        <p>Ein echter Mehrwert für Ihre Mitarbeitenden. Nachhaltig für Ihr Unternehmen.</p>
      </div>
    </div>
    <div class="teal-bar">Eine Investition <span class="dot">•</span> Mehrfache Wirkung <span class="dot">•</span> Nachhaltiger Nutzen</div>
  </div>
</section>

</body>
</html>
```